Corporate Business Card

Very professional, Modern, Not to busy, include phone address email, website
(253) 617-4930, 18761 52nd Avenue S, Kent, WA 98047, martin@plumlinegroup.com, varkoworks.com

Target Market(s)

Manufacturing

Industry/Entity Type

Aero, machining, manufacturing, Off road racing

Contact Information for Business Card

Phone, address email, website

```html
<!DOCTYPE html>
<html lang="en">
<head>
<meta charset="utf-8">
<title>Varko Works — Business Card</title>
<link href="https://fonts.googleapis.com/css2?family=Montserrat:wght@400;500;700;800&display=swap" rel="stylesheet">
<style>
  :root {
    --navy: #17366f;
    --navy-raised: #1f4387;
    --red: #d3222a;
    --white: #ffffff;
    --ink: #111111;
    --backdrop: #2a2a2a;
  }
  * { box-sizing: border-box; margin: 0; padding: 0; }
  html, body { width: 1200px; height: 1015px; overflow: hidden; }
  body {
    background: var(--backdrop);
    font-family: "Montserrat", Arial, sans-serif;
    position: relative;
  }
  .card {
    position: absolute;
    left: 250px;
    width: 700px;
    height: 400px;
    overflow: hidden;
    box-shadow: 0 10px 30px rgba(0,0,0,.45);
  }

  /* Back side */
  .card-back { top: 60px; background: var(--navy); }
  .card-back .brand-name {
    position: absolute; left: 0; right: 0; top: 160px;
    text-align: center;
    font-weight: 800; font-size: 58px; letter-spacing: 3px;
    color: var(--navy-raised);
  }

  /* Front side */
  .card-front { top: 555px; background: var(--white); }
  .front-top {
    position: absolute; left: 0; top: 0; width: 100%; height: 200px;
    background: var(--navy);
  }
  .front-top .brand-name {
    position: absolute; left: 0; right: 0; top: 70px;
    text-align: center;
    font-weight: 800; font-size: 50px; letter-spacing: 3px;
    color: var(--white);
  }
  .contact-band {
    position: absolute; left: 0; top: 200px; width: 100%; height: 100px;
    background: var(--red);
    color: var(--white);
  }
  .person {
    position: absolute; right: 380px; top: 24px; text-align: right;
  }
  .person-name { font-weight: 700; font-size: 26px; letter-spacing: .5px; line-height: 1.1; }
  .person-role { font-weight: 500; font-size: 17px; }
  .band-divider {
    position: absolute; left: 338px; top: 18px; width: 1.5px; height: 64px;
    background: var(--white);
  }
  .contact-list {
    position: absolute; left: 358px; top: 16px; list-style: none;
    font-size: 15px; font-weight: 500; line-height: 23px;
  }
  .contact-list li { display: flex; align-items: center; gap: 8px; }
  .contact-list svg { width: 15px; height: 15px; flex: none; }
  .address {
    position: absolute; left: 0; right: 0; top: 314px; text-align: center;
    font-size: 19px; font-weight: 500; color: var(--ink);
  }
  .accent-stripe {
    position: absolute; top: 352px; height: 7px;
  }
  .accent-stripe.navy { left: 0; width: 55%; background: var(--navy); }
  .accent-stripe.red { left: 55.6%; right: 0; background: var(--red); }
  .base-edge {
    position: absolute; left: 0; right: 0; bottom: 0; height: 12px;
    background: var(--navy);
  }
</style>
</head>
<body>

  <section class="card card-back" aria-label="Card back">
    <div class="brand-name">VARKO WORKS</div>
  </section>

  <section class="card card-front" aria-label="Card front">
    <div class="front-top">
      <div class="brand-name">VARKO WORKS</div>
    </div>

    <div class="contact-band">
      <div class="person">
        <div class="person-name">DANIEL REYES</div>
        <div class="person-role">Managing Director</div>
      </div>
      <div class="band-divider"></div>
      <ul class="contact-list">
        <li>
          <svg viewBox="0 0 24 24" fill="none" stroke="currentColor" stroke-width="2.2" stroke-linecap="round" stroke-linejoin="round"><path d="M22 16.9v3a2 2 0 0 1-2.2 2 19.8 19.8 0 0 1-8.6-3.1 19.5 19.5 0 0 1-6-6A19.8 19.8 0 0 1 2.1 4.2 2 2 0 0 1 4.1 2h3a2 2 0 0 1 2 1.7c.1.9.4 1.8.7 2.7a2 2 0 0 1-.5 2.1L8 9.8a16 16 0 0 0 6 6l1.3-1.3a2 2 0 0 1 2.1-.4c.9.3 1.8.6 2.7.7a2 2 0 0 1 1.7 2z"/></svg>
          (253) 617-4930
        </li>
        <li>
          <svg viewBox="0 0 24 24" fill="none" stroke="currentColor" stroke-width="2.2" stroke-linejoin="round"><rect x="2" y="5" width="20" height="14"/><path d="M2 5l10 8 10-8"/></svg>
          martin@plumlinegroup.com
        </li>
        <li>
          <svg viewBox="0 0 24 24" fill="none" stroke="currentColor" stroke-width="2"><circle cx="12" cy="12" r="10"/><path d="M2 12h20M12 2c3 3 3 17 0 20M12 2c-3 3-3 17 0 20"/></svg>
          www.varkoworks.com
        </li>
      </ul>
    </div>

    <p class="address">18761 52nd Avenue S, Kent, WA 98047</p>
    <div class="accent-stripe navy"></div>
    <div class="accent-stripe red"></div>
    <div class="base-edge"></div>
  </section>

</body>
</html>
```